Vernac Law Business cards and stationary design project

We are looking for a stationary design for business cards (double sided), 8x10, 5x7, and legal and standard envelopes.

We would like the design to match the logo that we have already.
Color palate preferred is Teal, White, grey and any others that will look good for a professional law firm.

We would like this statement: "RELATIONSHIPS. RESPECT. RESULT" to be on the back of the business cards and maybe on the stationary if it looks good.

Please see link to website for more information: www.vernac-law.example

Target Market(s)

Potential clients that need Attorney services.

Industry/Entity Type

Law Firm

Contact Information for Business Card

We would like the front and back to be two different colors. Current business cards are teal front, grey back and are a vertical design. We are open to options with colors.

Font styles to use
Serif

Colors
33a6d7
33b8a4
b9b9b9
5c5c5c

Requirements
Must have
• Logo supplied needs to go on the card and stationary.
• Match website color palate, www.vernac-law.example
• Be professional and not too wordy.
• Criminal Law, Civil Litigation, Personal Injury, Restraining Orders need to be on the card.
Nice to have
• RELATIONSHIPS. RESPECT. RESULTS. on the back of the card.
Should not have
• Not be too busy/wordy or too flashy.

```html
<!DOCTYPE html>
<html lang="en">
<head>
<meta charset="utf-8">
<title>Vernac Law – Business Card</title>
<link rel="stylesheet" href="https://fonts.googleapis.com/css2?family=Cinzel:wght@400&family=Open+Sans:wght@400;600&display=swap">
<style>
  :root {
    --teal: #1a8a97;
    --teal-dark: #127582;
    --white: #ffffff;
    --paper: #f7f7f7;
    --ink: #2b2b2b;
    --stage: #e6e6e6;
  }
  * { margin: 0; padding: 0; box-sizing: border-box; }
  html, body { width: 1200px; height: 844px; overflow: hidden; }
  body {
    background: var(--stage);
    font-family: "Open Sans", Arial, sans-serif;
    color: var(--ink);
  }
  .stage {
    width: 1200px; height: 844px;
    display: flex; align-items: center; justify-content: center; gap: 60px;
  }
  .card {
    position: relative;
    width: 490px; height: 280px;
    box-shadow: 0 6px 18px rgba(0,0,0,.18);
    overflow: hidden;
  }
  /* Front */
  .card-front { background: var(--paper); }
  .brand {
    position: absolute; top: 70px; right: 40px;
    display: flex; align-items: center; gap: 12px;
  }
  .brand-square { width: 14px; height: 14px; background: var(--teal); }
  .brand-name {
    font-family: "Cinzel", Georgia, serif;
    font-size: 34px; color: var(--teal); letter-spacing: 1px;
  }
  .contact { position: absolute; left: 34px; bottom: 26px; font-size: 14px; line-height: 1.3; }
  .contact-name { font-weight: 600; font-size: 17px; color: var(--teal); }
  .contact-title { margin-bottom: 12px; }
  .contact-address { margin-bottom: 10px; }
  .contact-list { list-style: none; }
  .contact-list li { display: flex; align-items: center; gap: 10px; height: 20px; }
  .contact-list svg { width: 12px; height: 12px; fill: var(--teal); flex: none; }
  /* Back */
  .card-back { background: var(--teal); color: var(--white); }
  .back-name {
    position: absolute; top: 70px; left: 0; right: 0; text-align: center;
    font-family: "Cinzel", Georgia, serif; font-size: 34px; letter-spacing: 1px;
  }
  .back-rule {
    position: absolute; top: 120px; left: 50%; width: 120px; margin-left: -60px;
    border-top: 1px solid rgba(255,255,255,.7);
  }
  .practice {
    position: absolute; top: 146px; left: 0; right: 0; text-align: center;
    font-size: 13px; line-height: 1.55;
  }
  .tagline-band {
    position: absolute; left: 0; right: 0; bottom: 0; height: 58px;
    background: var(--white);
    display: flex; align-items: center; justify-content: center;
  }
  .tagline {
    color: var(--teal-dark); font-weight: 600; font-size: 14px; letter-spacing: .5px;
  }
</style>
</head>
<body>
<main class="stage">
  <section class="card card-front">
    <div class="brand">
      <span class="brand-square"></span>
      <span class="brand-name">Vernac Law</span>
    </div>
    <div class="contact">
      <p class="contact-name">Daniel Avery</p>
      <p class="contact-title">Managing Director</p>
      <p class="contact-address">12345, Address Goes Here<br>Country Name, 123456</p>
      <ul class="contact-list">
        <li><svg viewBox="0 0 12 12"><path d="M2.5 0.5l2 2.3-1 1.3c.7 1.6 1.8 2.7 3.4 3.4l1.3-1 2.3 2-1.2 2.5C4.6 10.8 1.2 7.4 0 2z"/></svg>(044)-456-7890</li>
        <li><svg viewBox="0 0 12 12"><rect x="1" y="4" width="10" height="7" rx="1"/><rect x="3" y="0.5" width="6" height="3"/></svg>123-456-7890</li>
        <li><svg viewBox="0 0 12 12"><path d="M0 2h12v8H0z M0 2l6 4.5L12 2" stroke="#fff" stroke-width=".8"/></svg>info@youremail.com</li>
        <li><svg viewBox="0 0 12 12"><circle cx="6" cy="6" r="6"/><path d="M0 6h12M6 0c-3 3-3 9 0 12M6 0c3 3 3 9 0 12" stroke="#fff" stroke-width=".7" fill="none"/></svg>www.website.com</li>
      </ul>
    </div>
  </section>

  <section class="card card-back">
    <p class="back-name">Vernac Law</p>
    <div class="back-rule"></div>
    <p class="practice">Practice areas, Criminal Law<br>Civil Litigation/Personal Injury, Restraining Orders</p>
    <div class="tagline-band">
      <p class="tagline">RELATIONSHIPS. RESPECT. RESULT</p>
    </div>
  </section>
</main>
</body>
</html>
```